International Petrochemical business needs a web design for Clearway Desk system

We need a web design for a "Clearway Desk" system for an international petrochemical company. The web site is used internally within the company. It is hosted by an internal department which provides government permit request service for other departments.

We would like to see designs of two pages using color light blue. (home page, internal page as attached).
Home Page:
1. Header has a background image and small animation. Header on home page can be taller than the header of the internal page.
2. Layout as attached.

Internal Page:
1. Header can use the same background image as the home page and can be shorter to utilize the page for content.
2. The blue icon behind every captions represent an icon. When user move mouse over this icon, it displays the caption in Thai language as a tooltip. This icon needs to be redesign.

The final design should communicate the followings:
- Excellent service provided system in terms of time and accurary
- Rapid growth of business via building petrochemical refinery plant
Updates

For Internal Page, the blue circle behind every captions represent an icon. When mouse over this icon, a tool tip showing the caption in Thai language is shown. Please also design this icon..

There are more feedbacks from customer as followed:

1. Banner should consists of 
    1.1 "Approved" stamp on paper
    1.2 An image of Garuda. It is used on every government documents in Thailand
    1.3 Image of petrochemical plant
2. Each menu item (Home, Permit, Search, etc) should have different colors. Drop down menu will use the same color as its parent menu item.
3. Overall tone of the web page should be light blue with background of the body the web page in white
4. "New Request" button should use green color with icon on it
5. Table header of each box in the body of the page should use dark blue background with text in white

Please kindly submit your revisions.
Thank you.

Industry/Entity Type

Business

Requirements
Must have
• 1. Design for 1024x768 screen resolution
2. Use light blue theme
3. Background of header where the company logo is must have white background

```html
<!DOCTYPE html>
<html lang="en">
<head>
<meta charset="utf-8">
<title>Clearway Desk – Home</title>
<link href="https://fonts.googleapis.com/css2?family=Open+Sans:wght@400;600;700&display=swap" rel="stylesheet">
<style>
:root{
  --page-blue:#5c9ff0;
  --navy:#27225f;
  --navy-text:#2b2870;
  --pill:#1ba1e2;
  --grey-band:#f3f3f3;
  --line:#dcdcdc;
  --text:#333;
  --muted:#8a8a8a;
  --green:#1f9a1f;
  --green-dark:#127512;
}
*{box-sizing:border-box;margin:0;padding:0}
html,body{width:822px;height:1200px;overflow:hidden}
body{background:var(--page-blue);font-family:"Open Sans",sans-serif;color:var(--text);position:relative}
.topbar{position:absolute;left:60px;top:16px;width:702px;height:60px;background:linear-gradient(#fff,#f2f2f2);border-radius:2px;box-shadow:0 1px 3px rgba(0,0,0,.2);display:flex;align-items:center;justify-content:space-between;padding:0 14px}
.brand{display:flex;align-items:center;gap:6px;color:#1a8fd8;font-weight:700;font-size:15px}
.brand-dot{width:26px;height:26px;border-radius:50%;background:#1a8fd8}
.nav{display:flex;align-items:center;font-size:10px;color:#333}
.nav a{color:inherit;text-decoration:none;padding:0 16px;border-left:1px solid #ddd;line-height:26px}
.nav a:nth-child(2){border-left:none}
.nav a:last-child{padding-right:0}
.nav a.active{background:var(--pill);color:#fff;border:1px solid #0d86c8;border-radius:10px;line-height:16px;padding:0 9px;margin-right:12px}
.banner{position:absolute;left:60px;top:76px;width:702px;height:246px;background:linear-gradient(180deg,#5c9ff0 0%,#3e79c9 55%,#2c5fae 75%,#4b8ce0 100%)}
.badge{position:absolute;top:186px;width:48px;height:48px;border-radius:50%;background:#2f75d0;border:2px solid #7fb3f2}
.content{position:absolute;left:60px;top:322px;width:702px;height:820px;background:#fff;overflow:hidden}
.news{height:50px;background:var(--grey-band);display:flex;align-items:center;padding:0 14px;font-size:10px}
.news .label{color:#222;white-space:nowrap}
.news .sep{margin:0 8px}
.news .msg{color:var(--muted);margin-left:6px;flex:1;white-space:nowrap;overflow:hidden}
.search{width:150px;height:17px;border-radius:3px;background:#c9c9c9;border:1px solid #b8b8b8;position:relative;margin-left:36px;flex:none}
.search svg{position:absolute;right:5px;top:3px}
.section{position:absolute;left:14px}
.section.right{left:358px;width:330px}
h2{font-weight:400;font-size:15px;color:#222;margin-bottom:12px}
table{border-collapse:collapse;width:100%;font-size:10px}
thead th{background:var(--navy);color:#fff;font-weight:400;text-align:left;height:28px;padding-left:10px;border-right:1px solid #3e3a80}
tbody td{height:27px;padding-left:10px;border-bottom:1px solid #e8e8e8;border-right:1px solid #e8e8e8;color:#444;white-space:nowrap}
tbody tr:nth-child(even) td{background:#fafafa}
td a{color:var(--navy-text)}
td.status{color:var(--navy-text)}
.box{border:1px solid var(--line);border-top:none}
.pager{height:20px;font-size:9px;color:var(--navy-text);padding-left:10px;display:flex;align-items:center;gap:10px}
.band{position:absolute;left:0;top:279px;width:702px;height:229px;background:var(--grey-band)}
.new-btn{position:absolute;left:358px;top:567px;width:330px;height:65px;background:linear-gradient(#2ead2e,var(--green));border:2px solid var(--green-dark);border-radius:2px;display:flex;align-items:center;gap:16px;padding-left:20px;color:#fff;font-weight:700;font-size:31px;text-decoration:none;white-space:nowrap}
.footer{position:absolute;left:60px;top:1154px;width:702px;height:33px;background:#fff;display:flex;align-items:center;justify-content:space-between;padding:0 14px;font-size:8.5px}
.footer nav a{color:#111;text-decoration:none;margin-right:6px}
</style>
</head>
<body>
<header class="topbar">
  <div class="brand"><span class="brand-dot"></span>DELTA REFINING</div>
  <nav class="nav">
    <a class="active" href="#">HOME</a><a href="#">PERMITS</a><a href="#">SEARCH</a><a href="#">REPORT</a><a href="#">ADMIN</a><a href="#">HELP</a>
  </nav>
</header>
<div class="banner" role="img" aria-label="Petrochemical refinery plant at dusk by the water">
  <span class="badge" style="left:598px" role="img" aria-label="Approved stamp badge"></span>
  <span class="badge" style="left:652px" role="img" aria-label="Government emblem badge"></span>
</div>

<main class="content">
  <div class="news"><span class="label">Latest News</span><span class="sep">|</span><span class="label">June 8, 2013</span><span class="msg">On sait depuis longtemps que travailler avec du texte lisible et contenant du sens</span>
    <div class="search"><svg width="10" height="10" viewBox="0 0 10 10"><circle cx="4" cy="4" r="3" fill="none" stroke="#fff" stroke-width="1.4"/><line x1="6.2" y1="6.2" x2="9" y2="9" stroke="#fff" stroke-width="1.4"/></svg></div>
  </div>

  <section class="section" style="top:64px;width:329px">
    <h2>New Request</h2>
    <div class="box"><table>
      <thead><tr><th style="width:109px">Request No.</th><th style="width:139px">Requested Date</th><th>Branch</th></tr></thead>
      <tbody>
        <tr><td><a href="#">56-0003</a></td><td>20-4-2013</td><td>GC 1</td></tr>
        <tr><td><a href="#">56-0004</a></td><td>21-4-2013</td><td>GC 2</td></tr>
        <tr><td><a href="#">56-0005</a></td><td>22-4-2013</td><td>GC 3</td></tr>
        <tr><td><a href="#">56-0006</a></td><td>23-4-2013</td><td>GC 4</td></tr>
      </tbody></table>
      <div class="pager">◂ <span>1</span><span>2</span><span>3</span><span>4</span> ▸</div></div>
  </section>

  <section class="section right" style="top:64px">
    <h2>My Working Request</h2>
    <div class="box"><table>
      <thead><tr><th style="width:109px">Request No.</th><th style="width:103px">Requested Date</th><th>Status</th></tr></thead>
      <tbody>
        <tr><td><a href="#">22-0200</a></td><td>25-3-2013</td><td class="status">Waiting for process</td></tr>
        <tr><td><a href="#">22-0210</a></td><td>24-3-2013</td><td class="status">in progress</td></tr>
        <tr><td><a href="#">55-0300</a></td><td>18-1-2013</td><td class="status">Incomplete document</td></tr>
        <tr><td><a href="#">55-0301</a></td><td>20-1-2013</td><td class="status">Cancel Requested</td></tr>
      </tbody></table>
      <div class="pager">◂ <span>1</span><span>2</span><span>3</span><span>4</span> ▸</div></div>
  </section>

  <div class="band"></div>
  <section class="section" style="top:298px;width:674px">
    <h2>Expiring Permits</h2>
    <div class="box"><table>
      <thead><tr><th style="width:112px">Permit No.</th><th style="width:112px">Expire Date</th><th style="width:113px">Permit Name</th><th style="width:111px">Branch</th><th style="width:112px">Required Time (Day)</th><th>Due Date</th></tr></thead>
      <tbody>
        <tr><td><a href="#">AB56007</a></td><td>20-4-2013</td><td><a href="#">Permit Name #10</a></td><td>GC 1</td><td>30</td><td>-40</td></tr>
        <tr><td><a href="#">BIO5502</a></td><td>21-4-2013</td><td><a href="#">Permit Name #20</a></td><td>GC 2</td><td>60</td><td>15</td></tr>
        <tr><td><a href="#">TS34821</a></td><td>22-4-2013</td><td><a href="#">Permit Name #30</a></td><td>GC 3</td><td>90</td><td>25</td></tr>
        <tr><td><a href="#">GD47515</a></td><td>23-4-2013</td><td><a href="#">Permit Name #40</a></td><td>GC 4</td><td>120</td><td>-90</td></tr>
      </tbody></table>
      <div class="pager">◂ <span>1</span><span>2</span><span>3</span><span>4</span> ▸</div></div>
  </section>

  <section class="section" style="top:536px;width:329px">
    <h2>My in Progress Requests</h2>
    <div class="box"><table>
      <thead><tr><th style="width:109px">Request No.</th><th style="width:103px">Requested Date</th><th>Status</th></tr></thead>
      <tbody>
        <tr><td><a href="#">56-0003</a></td><td>20-4-2013</td><td class="status">Waiting for process</td></tr>
        <tr><td><a href="#">56-0004</a></td><td>21-4-2013</td><td class="status">in progress</td></tr>
        <tr><td><a href="#">56-0005</a></td><td>22-4-2013</td><td class="status">Incomplete document</td></tr>
        <tr><td><a href="#">56-0006</a></td><td>23-4-2013</td><td class="status">Cancel Requested</td></tr>
        <tr><td><a href="#">56-0007</a></td><td>24-4-2013</td><td class="status">In progress</td></tr>
        <tr><td><a href="#">56-0008</a></td><td>25-4-2013</td><td class="status">Cancel Requested</td></tr>
        <tr><td><a href="#">56-0009</a></td><td>25-4-2013</td><td class="status">Cancel Requested</td></tr>
      </tbody></table>
      <div class="pager">◂ <span>1</span><span>2</span><span>3</span><span>4</span> ▸</div></div>
  </section>

  <a class="new-btn" href="#">
    <svg width="54" height="46" viewBox="0 0 54 46" fill="none" stroke="#fff" stroke-width="2.5"><rect x="3" y="16" width="44" height="26" rx="3"/><line x1="10" y1="34" x2="40" y2="34"/><path d="M18 28 L40 6 L46 12 L24 34 L16 36 Z"/></svg>
    NEW REQUEST
  </a>

  <section class="section right" style="top:646px">
    <h2>Recent Completed Requests</h2>
    <div class="box"><table>
      <thead><tr><th style="width:164px">Request No.</th><th>Completed Date</th></tr></thead>
      <tbody>
        <tr><td><a href="#">22-0200</a></td><td>25-3-2013</td></tr>
        <tr><td><a href="#">22-0210</a></td><td>24-3-2013</td></tr>
        <tr><td><a href="#">55-0300</a></td><td>18-1-2013</td></tr>
      </tbody></table>
      <div class="pager">◂ <span>1</span><span>2</span><span>3</span><span>4</span> ▸</div></div>
  </section>
</main>

<footer class="footer">
  <nav><a href="#">Home</a><a href="#">Permits</a><a href="#">Search</a><a href="#">Report</a><a href="#">Admin</a><a href="#">Help</a></nav>
  <span>© Copyrights 2013 All rights Reserved</span>
</footer>
</body>
</html>
```